Flyer Vacation Gift Certificate

I need to create a beautiful flyer 8.5 x 11 PDF format flyer design. <br/><br/>Instructions:<br/>The flyer will really be a gift voucher for a las vegas vacation getaway. So must have a Las Vegas Theme exciting fun<br/><br/>The voucher should have two modules that will be editable. <br/>Must have a "Compliments Of" area and also must have an "Exclusively For" area<br/><br/>Keep in mind that this flyer will be printed so keep that in mind :)<br/><br/>Here the is the content for the vacation voucher:<br/><br/>There is no doubt that Las Vegas is one of the hottest travel destinations around the world. In fact, some people would even go as far as<br/>saying that perhaps it is THE hottest place to visit. Enjoy up to 4 nights of resort/casino accommodations in exciting Las Vegas, NV. Millions of people travel to this exciting city each year to enjoy its thrills. Thanks to the business you received this certificate from, now you can enjoy exciting Las Vegas, NV too!<br/><br/>Features:<br/>*Travel 7 Days A Week<br/>*Stay Your Choice Of Nights (1-4 Nights)<br/>*Good For Two Adults & Two Children<br/>*Pay Just The Taxes & Fees<br/>*Multiple Travel Date Requests Allowed<br/>*Fully Transferable To Another Person<br/>*Just A 30 Days Advance Notice Required<br/>*You Will Have 12 Months To Complete Travel After Redemption<br/><br/>HOW CAN WE DO THIS?<br/><br/>We contract with the world leading hotel chains and resorts to help them fill their otherwise empty rooms.<br/><br/>We help fill empty rooms which the hotels, resorts and cruise lines turn into additional revenue from other areas of their property and future bookings.<br/><br/>Hotels rarely experience full occupancy, yet they remain open, providing rooms and services at fixed costs. So when hotels give out their rooms by partnering with marketing companies like us, they might miss out on the room fee, but they already didn't have that in the first place, at least now they have the opportunity to gain a customer for their in-house restaurants, room service, their casinos, an extra day stay, future bookings, etc.<br/><br/>VIEW ALL THE DETAILS OF THIS SPECIAL OFFER AND REDEEM ONLINE AT <br/>WWW.QOTAVERNIX.COM<br/><br/>Certificate ID # 47261-38157<br/>Expires 02/29/2020<br/><br/><br/>*terms and conditions apply see website for details<br/><br/>KEEP IN MIND THE EXAMPLES I AM UPLOADING ARE SIMPLY TO SHOW YOU THAT THEY CONTAIN THE "COMPLIMENTS OF" AND "EXCLUSIVELY FOR" ELEMENTS. THESE MUST BE INCLUDED IN NEW DESIGN. PLEASE ONLY USE THE CONTENT I PROVIDED IN BRIEF, DONT USE CONTENT FROM EXAMPLES.

Target Market(s)

CONSUMERS THAT HAVE BEEN REWARDED WITH A VACATION CERTIFICATE FOR DOING BUSINESS WITH A COMPANY.

COMPANIES USE THESE AS MARKETING INCENTIVES TO ATTRACT MORE CUSTOMERS AND TO REWARD LOYALTY, ETC.

Industry/Entity Type

Travel Industry

Colors

Designer to choose colors to be used in the design.

Requirements
Must have
• I need to create a beautiful flyer 8.5 x 11 PDF format flyer design.
• Instructions:
• The flyer will really be a gift voucher for a las vegas vacation getaway. So must have a Las Vegas Theme exciting fun
• The voucher should have two modules that will be editable.
• Must have a "Compliments Of" area and also must have an "Exclusively For" area
• Keep in mind that this flyer will be printed so keep that in mind :)
• Here the is the content for the vacation voucher:
• There is no doubt that Las Vegas is one of the hottest travel destinations around the world. In fact, some people would even go as far as
• saying that perhaps it is THE hottest place to visit. Enjoy up to 4 nights of resort/casino accommodations in exciting Las Vegas, NV. Millions of people travel to this exciting city each year to enjoy its thrills. Thanks to the business you received this certificate from, now you can enjoy exciting Las Vegas, NV too!
• Features:
• *Travel 7 Days A Week
• *Stay Your Choice Of Nights (1-4 Nights)
• *Good For Two Adults & Two Children
• *Pay Just The Taxes & Fees
• *Multiple Travel Date Requests Allowed
• *Fully Transferable To Another Person
• *Just A 30 Days Advance Notice Required
• *You Will Have 12 Months To Complete Travel After Redemption
• HOW CAN WE DO THIS?
• We contract with the world leading hotel chains and resorts to help them fill their otherwise empty rooms.
• We help fill empty rooms which the hotels, resorts and cruise lines turn into additional revenue from other areas of their property and future bookings.
• Hotels rarely experience full occupancy, yet they remain open, providing rooms and services at fixed costs. So when hotels give out their rooms by partnering with marketing companies like us, they might miss out on the room fee, but they already didn't have that in the first place, at least now they have the opportunity to gain a customer for their in-house restaurants, room service, their casinos, an extra day stay, future bookings, etc.
• VIEW ALL THE DETAILS OF THIS SPECIAL OFFER AND REDEEM ONLINE AT
• WWW.QOTAVERNIX.COM
• Certificate ID # 47261-38157
• Expires 02/29/2020
• *terms and conditions apply see website for details
• KEEP IN MIND THE EXAMPLES I AM UPLOADING ARE SIMPLY TO SHOW YOU THAT THEY CONTAIN THE "COMPLIMENTS OF" AND "EXCLUSIVELY FOR" ELEMENTS. THESE MUST BE INCLUDED IN NEW DESIGN. PLEASE ONLY USE THE CONTENT I PROVIDED IN BRIEF, DONT USE CONTENT FROM EXAMPLES.
Nice to have
• EXCITING LAS VEGAS IMAGES THAT MAKE SOMEONE WANT TO GO THERE

```html
<!DOCTYPE html>
<html lang="en">
<head>
<meta charset="utf-8">
<title>Las Vegas Vacation Getaway Gift Voucher</title>
<link rel="stylesheet" href="https://fonts.googleapis.com/css2?family=Open+Sans:wght@400;600;700&family=Roboto+Slab:wght@700&family=Titan+One&family=Dancing+Script:wght@700&family=Kalam:wght@700&display=swap">
<style>
  :root{
    --stage:#3a3a3d;
    --paper:#f7f7fa;
    --navy:#27307a;
    --navy-deep:#1c2360;
    --red:#d12a2f;
    --coral:#e5574a;
    --gold:#e3a51c;
    --orange:#f2a516;
    --ink:#3a3a3a;
    --white:#ffffff;
  }
  *{box-sizing:border-box;margin:0;padding:0}
  html,body{width:1200px;height:800px;overflow:hidden;background:var(--stage)}
  .canvas{position:relative;width:1200px;height:800px}
  .voucher{
    position:absolute;left:300px;top:10px;width:600px;height:780px;
    background:var(--paper);overflow:hidden;font-family:"Open Sans",sans-serif;color:var(--ink);
  }
  .abs{position:absolute}
  .hero-photo{
    left:0;top:0;width:600px;height:340px;
    background:
      radial-gradient(ellipse at 28% 55%, rgba(230,70,90,.55), transparent 45%),
      radial-gradient(ellipse at 60% 70%, rgba(245,160,60,.45), transparent 40%),
      linear-gradient(180deg,#07060f 0%,#2a1640 45%,#5b2a63 75%,#2b1a3e 100%);
  }
  .shapes{left:0;top:0}
  .photo-circle{border-radius:50%;border:5px solid var(--white);box-shadow:0 2px 6px rgba(0,0,0,.25)}
  .circle-casino{left:355px;top:45px;width:230px;height:230px;
    background:radial-gradient(circle at 45% 45%,#c9887a 0%,#7a3a3a 35%,#2b1f2c 70%,#151218 100%)}
  .circle-slots{left:323px;top:283px;width:124px;height:124px;
    background:radial-gradient(circle at 45% 40%,#e8b49a 0%,#b4485a 40%,#4a2036 100%)}
  .circle-canal{left:467px;top:340px;width:116px;height:116px;
    background:linear-gradient(180deg,#5d8fd8 0%,#b9cce8 40%,#c59a6e 65%,#3d3a3a 100%)}

  .title-script{left:32px;top:268px;font-family:"Dancing Script",cursive;font-size:30px;color:var(--gold);line-height:1}
  .title-main{left:30px;top:300px;font-family:"Titan One",sans-serif;font-size:46px;color:var(--white);letter-spacing:2px;line-height:1}
  .title-sub{left:92px;top:356px;font-family:"Roboto Slab",serif;font-weight:700;font-size:24px;color:var(--coral);line-height:1}

  .intro{left:30px;top:428px;width:300px;font-size:8.5px;line-height:11px}
  .heading{font-family:"Kalam",cursive;font-weight:700;color:var(--ink);line-height:1}
  .features-title{left:30px;top:520px;font-size:16px}
  .how-title{left:30px;top:612px;font-size:15px;letter-spacing:.5px}

  .ticks{list-style:none;font-size:8.5px;line-height:11px}
  .ticks li{position:relative;padding-left:14px;margin-bottom:2px}
  .ticks li::before{content:"";position:absolute;left:0;top:2px;width:8px;height:8px;border:1.2px solid var(--red);border-radius:1px}
  .ticks li::after{content:"";position:absolute;left:3px;top:1px;width:3px;height:6px;border:solid var(--red);border-width:0 1.6px 1.6px 0;transform:rotate(40deg)}
  .features-left{left:30px;top:542px;width:280px}
  .features-right{left:355px;top:470px;width:220px}
  .features-right li{margin-bottom:5px}

  .how-list{left:30px;top:632px;width:540px;list-style:none;font-size:8px;line-height:10.5px}
  .how-list li{position:relative;padding-left:14px;margin-bottom:2px}
  .how-list li::before{content:"";position:absolute;left:0;top:1.5px;width:8px;height:8px;border-radius:50%;background:var(--red)}
  .how-list li::after{content:"";position:absolute;left:3px;top:2.5px;width:2px;height:4px;border:solid var(--white);border-width:0 1.2px 1.2px 0;transform:rotate(40deg)}

  .field{top:724px;display:flex;align-items:flex-end;gap:6px;font-size:9px;font-weight:700;letter-spacing:.5px;color:var(--ink)}
  .field .line{flex:1;border-bottom:1.5px dotted var(--ink);height:9px}
  .field-for{left:30px;width:270px}
  .field-from{left:320px;width:255px}

  .footer-expiry{left:22px;top:756px;font-size:12px;font-weight:700;color:var(--gold)}
  .footer-expiry span{font-weight:400;color:var(--white)}
  .footer-id{left:170px;top:756px;font-size:12px;font-weight:700;color:var(--gold)}
  .footer-id span{font-weight:400;color:var(--white)}
  .footer-web{left:392px;top:756px;display:flex;align-items:center;gap:6px;font-size:11px;font-weight:600;color:var(--white);letter-spacing:.3px}
</style>
</head>
<body>
<div class="canvas">
  <div class="voucher">
    <div class="abs hero-photo" role="img" aria-label="Night photo of the Las Vegas welcome sign with neon lights and light trails on the Strip"></div>

    <svg class="abs shapes" width="600" height="780" viewBox="0 0 600 780" aria-hidden="true">
      <path d="M0,312 Q270,262 600,248 L600,335 Q450,338 355,398 Q210,420 0,420 Z" fill="var(--navy)"/>
      <path d="M330,412 Q460,340 600,330" fill="none" stroke="var(--orange)" stroke-width="5"/>
      <path d="M0,750 L340,750 L328,780 L0,780 Z" fill="var(--red)"/>
      <path d="M0,745 L345,745 L343,750 L0,750 Z" fill="var(--navy)"/>
      <path d="M350,780 L364,748 Q368,742 378,742 L600,738 L600,780 Z" fill="var(--navy)"/>
    </svg>

    <div class="abs photo-circle circle-casino" role="img" aria-label="Photo of friends celebrating at a casino table with poker chips flying"></div>
    <div class="abs photo-circle circle-slots" role="img" aria-label="Photo of friends cheering at a slot machine"></div>
    <div class="abs photo-circle circle-canal" role="img" aria-label="Photo of a Venetian style resort canal with a gondola under blue sky"></div>

    <div class="abs title-script">Gift voucher</div>
    <div class="abs title-main">LAS VEGAS</div>
    <div class="abs title-sub">vacation getaway</div>

    <p class="abs intro">There is no doubt that Las Vegas is one of the hottest travel destinations around the world. In fact, some people would even go as far as saying that perhaps it is THE hottest place to visit. Enjoy up to 4 nights of resort/casino accommodations in exciting Las Vegas, NV. Millions of people travel to this exciting city each year to enjoy its thrills. Thanks to the business you received this certificate from, now you can enjoy exciting Las Vegas, NV too!</p>

    <ul class="abs ticks features-right">
      <li>Fully Transferable To Another Person</li>
      <li>Just A 30 Days Advance Notice Required</li>
      <li>You Will Have 12 Months To Complete Travel After Redemption</li>
    </ul>

    <h2 class="abs heading features-title">Features :</h2>
    <ul class="abs ticks features-left">
      <li>Travel 7 Days A Week</li>
      <li>Stay Your Choice Of Nights (1-4 Nights)</li>
      <li>Good For Two Adults &amp; Two Children</li>
      <li>Pay Just The Taxes &amp; Fees</li>
      <li>Multiple Travel Date Requests Allowed</li>
    </ul>

    <h2 class="abs heading how-title">HOW CAN WE DO THIS ?</h2>
    <ul class="abs how-list">
      <li>We contract with the world leading hotel chains and resorts to help them fill their otherwise empty rooms.</li>
      <li>We help fill empty rooms which the hotels, resorts and cruise lines turn into additional revenue from other areas of their property and future bookings.</li>
      <li>Hotels rarely experience full occupancy, yet they remain open, providing rooms and services at fixed costs. So when hotels give out their rooms by partnering with marketing companies like us, they might miss out on the room fee, but they already didn't have that in the first place, at least now they have the opportunity to gain a customer for their in-house restaurants, room service, their casinos, an extra day stay, future bookings, etc.</li>
    </ul>

    <div class="abs field field-for">EXCLUSIVELY FOR :<span class="line"></span></div>
    <div class="abs field field-from">COMPLIMENTS OF :<span class="line"></span></div>

    <div class="abs footer-expiry">Expires <span>02/29/2020</span></div>
    <div class="abs footer-id">Certificate ID <span># 47261-38157</span></div>
    <div class="abs footer-web">
      <svg width="12" height="12" viewBox="0 0 12 12" aria-hidden="true">
        <circle cx="6" cy="6" r="5.3" fill="var(--gold)"/>
        <ellipse cx="6" cy="6" rx="2.3" ry="5.3" fill="none" stroke="var(--navy)" stroke-width=".8"/>
        <line x1=".7" y1="6" x2="11.3" y2="6" stroke="var(--navy)" stroke-width=".8"/>
      </svg>
      WWW.QOTAVERNIX.COM
    </div>
  </div>
</div>
</body>
</html>
```